Lone Star Wetland Flora Stewardship Guild

We need to design the home page of this new website. We would like a fun website design for provides as a resource for members and information for potential members.
Please design so that we can see a portion of background on each side on the website.
I just need the final design files psd no coding needed.
Attached is their logo (colors are not 100% set in stone either so can mess with those as I did in the quick mockup attached)
Attached is a pdf newsletter they send out, you can get a feel for them and what they are about. The design is crappy and we are here to fix that going forward and we are starting with the website.
Here are some quick example websites (design style is open)
- I attached a quick mockup i did just for a content visual but by all means do what you want.
- http://www.brightpathleaders.example/
- http://www.civicunityhub.example/
- http://preview.webskinvault.example/show.php?cat=layouts&host=skinbazaar&temp=novaline
- http://www.meadowkeep.example/
- http://www.urbangleaners.example/
- http://www.projectcozyknit.example/
here are some of the other chapters website (pretty bad!)
and here are some of the others:
- http://www.dwrvcs.example/
- http://kwfg.example/
- http://www.blvcg.example/
Content Items that need to be included:
1. Logo
2. Menu - home, about, members, resources, events, membership, contact
3. Become a member - button or action
4. social links - chatterloop, workweave, clipstream
5. banner - that needs to explain their purpose "Promoting environmental stewardship through operations, research, education and outreach" (or this can be worked into the design)
6. Upcoming event (s)
7. Advertisement - members can place an ad on the website, this can be a placeholder for now
8. newsletter signup
9. advertise with us - this link can be in the footer
30-60 years of age, succesfull (household budgets of 120K+ men and women that live in texas.
Education

```html
<!DOCTYPE html>
<html lang="en">
<head>
<meta charset="utf-8">
<title>Lone Star Wetland Flora Stewardship Guild</title>
<link rel="stylesheet" href="https://fonts.googleapis.com/css2?family=Questrial&family=Cabin:wght@400;500;600&family=Arimo:wght@400&display=swap">
<style>
:root{
  --navy:#0d2260;
  --crimson:#b0223f;
  --heading:#9b2346;
  --text:#3a3a3a;
  --white:#ffffff;
  --footer:#0f0b09;
  --rule:#d9d9d9;
}
*{margin:0;padding:0;box-sizing:border-box}
html,body{width:1098px;height:1200px;overflow:hidden}
body{position:relative;font-family:"Cabin",sans-serif;color:var(--text);background:var(--footer)}
.backdrop{position:absolute;inset:0;background:linear-gradient(180deg,#6f9fd6 0%,#b9d2ee 14%,#8db6e0 24%,#5f8c6a 33%,#6e93a6 42%,#36493a 52%,#1a1410 62%,#120d0a 100%)}
.top-rule{position:absolute;left:0;top:0;width:1098px;height:3px;background:var(--crimson)}
.a{position:absolute}
.social{top:12px;left:580px;display:flex;gap:11px}
.social a{width:24px;height:24px;border-radius:50%;background:var(--navy);display:block}
.social a.clipstream{background:var(--crimson)}
.login{top:14px;left:707px;font-family:"Questrial",sans-serif;font-size:18px;color:#222;display:flex;align-items:center;gap:6px}
.become{top:3px;left:804px;width:202px;height:37px;background:var(--crimson);color:#fff;font-family:"Questrial",sans-serif;font-size:17px;letter-spacing:.5px;display:flex;align-items:center;justify-content:center}
.brand{top:50px;left:95px;display:flex;align-items:center;gap:8px;font-family:"Questrial",sans-serif;font-size:40px;color:var(--crimson)}
.brand i{width:26px;height:26px;background:var(--navy);border-radius:50%;display:block}
.site-title{top:64px;left:350px;font-family:"Questrial",sans-serif;font-size:28px;color:#111}
.nav{top:114px;left:325px}
.underline{top:156px;left:91px;width:260px;height:4px;background:var(--navy)}
.menu{top:114px;left:325px;width:681px;height:46px;display:flex;align-items:center;padding-left:38px;font-family:"Arimo",sans-serif;font-size:13px;color:#fff}
.menu a{color:#fff;text-decoration:none;padding:5px 11px;margin-right:10px}
.menu a.current{background:var(--crimson)}
.hero{top:160px;left:91px;width:915px;height:385px;background:linear-gradient(180deg,#7fb0b5 0%,#5f9a96 35%,#3e6e69 65%,#2b4a4a 100%)}
.caption{top:467px;left:91px;width:915px;height:78px;background:rgba(10,14,14,.82)}
.caption p{position:absolute;left:16px;top:12px;font-family:"Questrial",sans-serif;font-size:22px;line-height:31px;color:#fff}
.pager{top:490px;left:845px;display:flex;gap:16px}
.pager b{width:21px;height:30px;background:var(--crimson);color:#fff;font-family:"Questrial",sans-serif;font-weight:400;font-size:23px;display:flex;align-items:center;justify-content:center}
.pager b.on{background:#e8e8e8;color:#111}
.content{top:545px;left:91px;width:915px;height:591px;background:var(--white)}
h2{position:absolute;font-family:"Questrial",sans-serif;font-weight:400;font-size:27px;color:var(--heading);letter-spacing:.5px}
.intro{top:610px;left:108px;width:585px;font-size:14.6px;line-height:20px}
.event{left:109px;width:585px}
.event .thumb{position:absolute;left:0;top:0;width:142px;height:94px}
.event h3{position:absolute;left:155px;top:0;font-family:"Cabin",sans-serif;font-weight:600;font-size:13.6px;color:var(--navy)}
.event .date{position:absolute;left:155px;top:22px;font-style:italic;font-size:13px;color:var(--crimson)}
.event p{position:absolute;left:156px;top:42px;width:430px;font-size:13.6px;line-height:17.5px}
.divider{top:922px;left:106px;width:588px;height:1px;background:var(--rule)}
.view-all{top:1068px;left:579px;width:114px;height:29px;background:var(--navy);border-radius:4px;color:#fff;font-family:"Questrial",sans-serif;font-size:15px;display:flex;align-items:center;justify-content:center}
.newsletter{top:573px;left:721px;width:267px;height:154px;background:var(--navy);border-radius:5px}
.newsletter h4{position:absolute;top:15px;left:0;width:100%;text-align:center;font-family:"Questrial",sans-serif;font-weight:400;font-size:24px;color:#fff}
.newsletter .field{position:absolute;top:57px;left:28px;width:209px;height:30px;background:#fff;font-family:"Arimo",sans-serif;font-size:13px;color:#333;padding:8px 7px}
.newsletter .sign{position:absolute;top:103px;left:138px;width:99px;height:31px;background:var(--crimson);color:#fff;font-family:"Cabin",sans-serif;font-weight:600;font-size:16px;display:flex;align-items:center;justify-content:center}
.ad{top:753px;left:722px;width:266px;height:345px;background:linear-gradient(180deg,#1f5f8f 0%,#143a5c 40%,#0d1a2a 78%,#e2e2e2 79%,#e2e2e2 100%)}
.footer-copy{top:1158px;left:92px;font-family:"Arimo",sans-serif;font-size:13px;color:#fff}
.footer-link{top:1159px;left:885px;font-family:"Arimo",sans-serif;font-size:15px;color:#fff;text-decoration:underline}
</style>
</head>
<body>
<div class="backdrop" role="img" aria-label="Background photograph of a Texas lake with lily pads and tree-lined shores under a blue sky"></div>
<div class="top-rule"></div>

<header>
  <nav class="a social" aria-label="Social links">
    <a class="chatterloop" aria-label="chatterloop" title="chatterloop"></a>
    <a class="workweave" aria-label="workweave" title="workweave"></a>
    <a class="clipstream" aria-label="clipstream" title="clipstream"></a>
  </nav>
  <div class="a login">
    <svg width="16" height="16" viewBox="0 0 16 16"><rect x="5" y="1.5" width="9" height="13" fill="none" stroke="#b0223f" stroke-width="1.6"/><path d="M1 8h8M6 5l3 3-3 3" fill="none" stroke="#b0223f" stroke-width="1.6"/></svg>
    Login
  </div>
  <div class="a become">BECOME A MEMBER</div>
  <div class="a brand"><i></i>LSWFSG</div>
  <div class="a site-title">Lone Star Wetland Flora Stewardship Guild</div>
  <svg class="a nav" width="681" height="46" viewBox="0 0 681 46"><path d="M28 0H681V46H0Z" fill="#0d2260"/></svg>
  <div class="a underline"></div>
  <nav class="a menu">
    <a class="current">HOME</a><a>ABOUT</a><a>MEMBERS</a><a>RESOURCES</a><a>EVENTS</a><a>MEMBERSHIP</a><a>CONTACT</a>
  </nav>
</header>

<div class="a hero" role="img" aria-label="Banner photograph of a white water lily among lily pads and reeds on a pond"></div>
<div class="a caption"><p>Promoting environmental stewardship through operations,<br>research, education and outreach</p></div>
<div class="a pager"><b class="on">1</b><b>2</b><b>3</b><b>4</b></div>

<main class="a content"></main>
<h2 style="top:568px;left:107px">Welcome to LSWFSG</h2>
<p class="a intro">The Lone Star Wetland Flora Stewardship Guild, Inc. is an organization of scientists, educators, students, commercial pesticide applicators, administrators, and concerned individuals interested in the management and study of aquatic plants. The membership reflects a diversity of federal, state, and local agencies; universities and colleges around the world; corporations; and small businesses.</p>

<h2 style="top:751px;left:107px">Upcoming Events</h2>
<article class="a event" style="top:805px">
  <div class="thumb" role="img" aria-label="Photograph of a pond with lily pads and trees" style="background:linear-gradient(180deg,#9cc3e6 0%,#cfe0ef 35%,#4f7a3a 55%,#5d6a55 75%,#3e4a30 100%)"></div>
  <h3>2014 Northeast Plant Stewardship Circle Annual Conference</h3>
  <div class="date">January 21, 2014 -January 23, 2014</div>
  <p>Lorem Ipsum is simply dummy text of the printing and typesetting industry. Lorem Ipsum has been the industry's standard dummy text ever since the 1500s,</p>
</article>
<div class="a divider"></div>
<article class="a event" style="top:945px">
  <div class="thumb" role="img" aria-label="Photograph of reeds and trees reflected in a pond" style="left:1px;background:linear-gradient(180deg,#e9eef0 0%,#9cb97a 35%,#5e8a3c 60%,#3f5a35 100%)"></div>
  <h3>2014 Northeast Plant Stewardship Circle Annual Conference</h3>
  <div class="date">January 21, 2014 -January 23, 2014</div>
  <p>Lorem Ipsum is simply dummy text of the printing and typesetting industry. Lorem Ipsum has been the industry's standard dummy text ever since the 1500s,</p>
</article>
<div class="a view-all">Veiw All</div>

<aside class="a newsletter">
  <h4>Newsletter Signup</h4>
  <div class="field">Email Address</div>
  <div class="sign">Sign Up</div>
</aside>
<div class="a ad" role="img" aria-label="Member advertisement placeholder showing algaecide product containers for ClearPond PRO by PureWater Labs"></div>

<footer>
  <div class="a footer-copy">Copyright © 2014 LSWFSG. All rights reserved.</div>
  <a class="a footer-link">advertise with us</a>
</footer>
</body>
</html>
```